RW Holloway LLC Business Card - Civil Engineering & Consulting Firm

We need a Business Card that is elegant, and masculine.  It is our Professional Civil Engineering & Consulting Company located in San Antonio TX (Not s construction or builder firm- no gears & no tool images please). We provide civil engineering services including  commercial site plans, grading and drainage plans, utility plans, hydraulics and hydrology, land planning, utility coordination, and other general civil engineering services related to commercial and residential development.
We have 2 existing Logos. We would like to convey reliability, strength, trustworthiness and attention to detail.  Blues and orange tones as per logo We are OK with the use of a darker blue in the mix.  We have 2 logo versions - Full Company Name Logo to go on the back of card, & Small Icon Logo for the front w/ personal Info.

Target Market(s)
Architects, Real Estate Developers, Other Strctural Engineers, Surveyers, General Contractors
Industry/Entity Type
Professional Civil Engineering
Contact Information for Business Card
Name, Position, Address, Cell & Office #, email, and company website
Font styles to use
Other font styles liked:
- Avian
Requirements
Should not have
- No Tools, No Gears, no Cranes, or Construction Equipment.

```html
<!DOCTYPE html>
<html lang="en">
<head>
<meta charset="utf-8">
<title>RW Holloway LLC – Business Card</title>
<link href="https://fonts.googleapis.com/css2?family=Montserrat:wght@300;400;500;700&display=swap" rel="stylesheet">
<style>
  :root {
    --stage: #8e8e8e;
    --sky: #74aedb;
    --amber: #e6943e;
    --orange: #e28a35;
    --ink: #1c1c1c;
    --paper: #f3f3f3;
    --facet-1: #e6e6e6;
    --facet-2: #dcdcdc;
    --facet-3: #ededed;
    --white: #ffffff;
  }
  * { box-sizing: border-box; margin: 0; padding: 0; }
  html, body { width: 1200px; height: 900px; overflow: hidden; }
  body {
    background: var(--stage);
    font-family: "Montserrat", sans-serif;
    display: flex;
    flex-direction: column;
    align-items: center;
    justify-content: center;
    gap: 64px;
  }
  .card {
    position: relative;
    width: 620px;
    height: 354px;
    border-radius: 26px;
    overflow: hidden;
    box-shadow: 0 10px 24px rgba(0,0,0,0.28);
  }

  /* Back of card */
  .card--back {
    background: linear-gradient(160deg, var(--sky) 0%, #b3a594 48%, var(--amber) 80%);
    display: flex;
    align-items: center;
    justify-content: center;
  }
  .brand-lockup { text-align: center; color: var(--white); }
  .brand-lockup__name {
    font-weight: 300;
    font-size: 44px;
    letter-spacing: 0.08em;
    text-transform: uppercase;
  }
  .brand-lockup__rule {
    height: 2px;
    background: var(--white);
    margin: 12px auto 14px;
    width: 100%;
  }
  .brand-lockup__tagline {
    font-weight: 300;
    font-size: 15px;
    letter-spacing: 0.42em;
    text-transform: uppercase;
  }

  /* Front of card */
  .card--front { background: var(--paper); }
  .facets { position: absolute; inset: 0; width: 100%; height: 100%; }
  .accent-bar {
    position: absolute;
    left: 0;
    top: 150px;
    width: 26px;
    height: 34px;
    background: var(--orange);
  }
  .profile {
    position: absolute;
    left: 56px;
    top: 140px;
    color: var(--ink);
  }
  .profile__name {
    color: var(--orange);
    font-weight: 700;
    font-size: 22px;
    letter-spacing: 0.02em;
    text-transform: uppercase;
  }
  .profile__role { font-size: 16px; font-weight: 500; margin-top: 2px; }
  .profile__address { font-size: 15px; line-height: 1.3; margin-top: 18px; }
  .contact-list { list-style: none; margin-top: 14px; }
  .contact-list li {
    display: flex;
    align-items: center;
    gap: 12px;
    font-size: 15px;
    line-height: 1.45;
  }
  .contact-list svg { width: 15px; height: 15px; fill: var(--orange); flex: none; }
  .front-mark {
    position: absolute;
    right: 44px;
    top: 56px;
    display: flex;
    align-items: center;
    gap: 10px;
    color: var(--orange);
    font-weight: 500;
    font-size: 20px;
  }
  .front-mark__square { width: 14px; height: 14px; background: var(--orange); }
</style>
</head>
<body>

  <section class="card card--back" aria-label="Card back">
    <div class="brand-lockup">
      <div class="brand-lockup__name">RW Holloway LLC</div>
      <div class="brand-lockup__rule"></div>
      <div class="brand-lockup__tagline">Consulting Engineers</div>
    </div>
  </section>

  <section class="card card--front" aria-label="Card front">
    <svg class="facets" viewBox="0 0 620 354" preserveAspectRatio="none" aria-hidden="true">
      <polygon points="0,0 620,0 620,40 260,150 0,120" fill="var(--facet-3)"/>
      <polygon points="260,150 620,40 620,200 420,230" fill="var(--facet-2)"/>
      <polygon points="0,120 260,150 420,230 300,354 0,354" fill="var(--facet-1)"/>
      <polygon points="420,230 620,200 620,354 300,354" fill="var(--facet-3)"/>
      <polygon points="330,0 470,0 420,230" fill="var(--facet-1)" opacity="0.7"/>
    </svg>

    <div class="front-mark">
      <span class="front-mark__square"></span>
      <span>RW Holloway LLC</span>
    </div>

    <div class="accent-bar"></div>

    <div class="profile">
      <div class="profile__name">Dane Whitford</div>
      <div class="profile__role">Co-Founder</div>
      <div class="profile__address">4180 Ridgeline Drive<br>Suite 210 Alamo Hts.12</div>
      <ul class="contact-list">
        <li>
          <svg viewBox="0 0 24 24"><path d="M6.6 10.8a15 15 0 0 0 6.6 6.6l2.2-2.2c.3-.3.7-.4 1-.2 1.1.4 2.3.6 3.6.6.6 0 1 .4 1 1V20c0 .6-.4 1-1 1A17 17 0 0 1 3 4c0-.6.4-1 1-1h3.5c.6 0 1 .4 1 1 0 1.3.2 2.5.6 3.6.1.3 0 .7-.2 1z"/></svg>
          555-014-2286
        </li>
        <li>
          <svg viewBox="0 0 24 24"><path d="M2 8c0-2 4-4 10-4s10 2 10 4v2h-5V8H7v2H2zM5 12h14l2 8H3zm7 2a2.5 2.5 0 1 0 0 5 2.5 2.5 0 0 0 0-5z"/></svg>
          555-014-7731
        </li>
        <li>
          <svg viewBox="0 0 24 24"><path d="M2 5h20v14H2zm2 2v.5l8 5.5 8-5.5V7z"/></svg>
          info@rwhollowayllc
        </li>
        <li>
          <svg viewBox="0 0 24 24"><path d="M12 2a10 10 0 1 0 0 20 10 10 0 0 0 0-20zm0 2c1 0 2.4 2 3 5H9c.6-3 2-5 3-5zM4.3 10h3.6a18 18 0 0 0 0 4H4.3a8 8 0 0 1 0-4zm5.6 0h4.2a16 16 0 0 1 0 4H9.9a16 16 0 0 1 0-4zm6.2 0h3.6a8 8 0 0 1 0 4h-3.6a18 18 0 0 0 0-4zM9 15h6c-.6 3-2 5-3 5s-2.4-2-3-5z"/></svg>
          www.rwhollowayeng.com
        </li>
      </ul>
    </div>
  </section>

</body>
</html>
```